10 Labels for Wild Bird Food

Label Design Request for New Products
We are excited to announce the launch of 10 new products and are seeking vibrant, fun, and colorful labels to match their energy. Each label should measure 6 x 4 inches (152.4mm x 101.6mm) and must feature our brand logo. Additionally, please include all the necessary information as detailed in the attached Word document.

Let's make our products stand out on the shelves with eye-catching designs!

Target Market(s)

Wild Bird Food Buyers

Requirements
Must have
• Logo

```html
<!DOCTYPE html>
<html lang="en">
<head>
<meta charset="utf-8">
<title>Wild Bird Food Labels – 5L Bag Range</title>
<link href="https://fonts.googleapis.com/css2?family=Montserrat:wght@800&family=Open+Sans:wght@400;600&family=Ubuntu:wght@500;700&display=swap" rel="stylesheet">
<style>
  :root{
    --teal:#17796f;
    --green:#8cc63f;
    --ink:#141414;
    --grey:#4a4a4a;
    --paper:#ffffff;
    --rule:#9cc86a;
    --dots:#8fc2b4;
  }
  *{margin:0;padding:0;box-sizing:border-box}
  html,body{width:904px;height:1202px;overflow:hidden;background:var(--paper)}
  .sheet{position:relative;width:904px;height:1202px}
  .defs{position:absolute;width:0;height:0}

  .label{position:absolute;width:246px;height:246px;border-radius:50%;
    background:conic-gradient(from var(--turn),
      var(--teal) 0%, var(--teal) 38%, var(--green) 55%, var(--green) 86%, var(--teal) 100%)}
  .face{position:absolute;left:12px;top:12px;width:222px;height:222px;border-radius:50%;background:var(--paper)}
  .mark-spot{position:absolute;left:30px;top:27px;width:38px;height:38px;border-radius:50%;background:var(--paper)}
  .rim-text{position:absolute;left:0;top:0;overflow:visible}
  .ring-copy{font-family:"Open Sans",sans-serif;font-weight:600;font-size:5.2px;fill:var(--grey)}

  .product-photo{position:absolute;left:48px;top:40px;width:150px;height:150px;border-radius:50%;opacity:.55}
  .bag-size,.title,.specs,.ean,.divider,.brand{position:absolute;left:0;width:246px;text-align:center}
  .bag-size{font-family:"Ubuntu",sans-serif;font-weight:700;font-size:14px;line-height:16px;letter-spacing:.5px;color:var(--teal)}
  .label.green-size .bag-size{color:var(--green)}
  .title{font-family:"Montserrat",sans-serif;font-weight:800;font-size:17.5px;line-height:21.5px;color:var(--ink);letter-spacing:.3px}
  .specs{font-family:"Open Sans",sans-serif;font-size:6.6px;line-height:9px;color:var(--ink);word-spacing:1px}
  .specs .sep{margin:0 6px}
  .ean{left:72px;width:auto;text-align:left;font-family:"Open Sans",sans-serif;font-size:6.6px;line-height:9px;color:var(--ink)}
  .divider{left:50px;width:146px;height:0;border-top:.7px solid var(--rule)}
  .brand{font-family:"Ubuntu",sans-serif;font-weight:500;font-size:13px;line-height:16px;color:var(--teal);letter-spacing:.3px}

  .label.two-line .bag-size{top:45px}
  .label.two-line .title{top:63px}
  .label.two-line .specs{top:113px}
  .label.two-line .ean{top:130px}
  .label.two-line .divider{top:153px}
  .label.two-line .brand{top:166px}

  .label.one-line .bag-size{top:59px}
  .label.one-line .title{top:77px}
  .label.one-line .specs{top:105px}
  .label.one-line .ean{top:122px}
  .label.one-line .divider{top:153px}
  .label.one-line .brand{top:166px}

  .page-code{position:absolute;left:840px;top:1183px;font-family:"Open Sans",sans-serif;font-size:7px;color:var(--teal)}
</style>
</head>
<body>
<div class="sheet">
  <svg class="defs" aria-hidden="true">
    <defs>
      <path id="copy-path" d="M -72.12 -72.12 A 102 102 0 1 1 72.12 72.12 A 102 102 0 1 1 -72.12 -72.12"/>
      <g id="label-copy" class="ring-copy">
        <circle r="90" fill="none" stroke="var(--dots)" stroke-width=".6" stroke-dasharray="1 1.6"/>
        <text text-anchor="middle"><textPath href="#copy-path" startOffset="18.9%">Marlow Imports, Brookside Mill Business Park, Elmford, EF12 3AB</textPath></text>
        <text text-anchor="middle"><textPath href="#copy-path" startOffset="34.7%">/</textPath></text>
        <text text-anchor="middle"><textPath href="#copy-path" startOffset="41.9%">Sales@marlowimports.co.uk</textPath></text>
        <text text-anchor="middle"><textPath href="#copy-path" startOffset="49.2%">/</textPath></text>
        <text text-anchor="middle"><textPath href="#copy-path" startOffset="56.4%">Not for human consumption</textPath></text>
        <text text-anchor="middle"><textPath href="#copy-path" startOffset="64.7%">|</textPath></text>
        <text text-anchor="middle"><textPath href="#copy-path" startOffset="69.4%">May Contain Nuts</textPath></text>
        <text text-anchor="middle"><textPath href="#copy-path" startOffset="75.3%">/</textPath></text>
        <text text-anchor="middle"><textPath href="#copy-path" startOffset="82.5%">Expiry Date: 12/09/2024</textPath></text>
        <text text-anchor="middle"><textPath href="#copy-path" startOffset="89.7%">|</textPath></text>
        <text text-anchor="middle"><textPath href="#copy-path" startOffset="93.3%">Batch: 8</textPath></text>
      </g>
    </defs>
  </svg>

  <section class="label two-line" style="left:53px;top:57px;--turn:-36deg">
    <div class="face"></div><div class="mark-spot"></div>
    <div class="product-photo" role="img" aria-label="Faded photo of a sunflower head" style="background:radial-gradient(circle,#f6dfa0,#fbefd0 60%,#fff)"></div>
    <svg class="rim-text" width="246" height="246" viewBox="-123 -123 246 246" aria-hidden="true"><use href="#label-copy"/></svg>
    <p class="bag-size">5L BAG</p>
    <h2 class="title">SUNFLOWER<br>HEARTS</h2>
    <p class="specs">SKU: HW21<span class="sep">|</span>Net Weight: 2900g</p>
    <p class="ean">EAN 13 BARCODE:</p>
    <div class="divider"></div>
    <p class="brand">perch &amp; peck</p>
  </section>

  <section class="label one-line green-size" style="left:333px;top:57px;--turn:209deg">
    <div class="face"></div><div class="mark-spot"></div>
    <div class="product-photo" role="img" aria-label="Faded photo of peanuts with leaves" style="background:radial-gradient(circle,#ead8bd,#f3e9d8 60%,#fff)"></div>
    <svg class="rim-text" width="246" height="246" viewBox="-123 -123 246 246" aria-hidden="true"><use href="#label-copy"/></svg>
    <p class="bag-size">5L BAG</p>
    <h2 class="title">PEANUTS</h2>
    <p class="specs">SKU: HW22<span class="sep">|</span>Net Weight: 3100g</p>
    <p class="ean">EAN 13 BARCODE:</p>
    <div class="divider"></div>
    <p class="brand">perch &amp; peck</p>
  </section>

  <section class="label two-line" style="left:613px;top:57px;--turn:-21deg">
    <div class="face"></div><div class="mark-spot"></div>
    <div class="product-photo" role="img" aria-label="Faded photo of dried mealworms" style="background:radial-gradient(circle,#e8d1aa,#f3e6cf 60%,#fff)"></div>
    <svg class="rim-text" width="246" height="246" viewBox="-123 -123 246 246" aria-hidden="true"><use href="#label-copy"/></svg>
    <p class="bag-size">5L BAG</p>
    <h2 class="title">DRIED<br>MEALWORMS</h2>
    <p class="specs">SKU: HW23<span class="sep">|</span>Net Weight: 800g</p>
    <p class="ean">EAN 13 BARCODE:</p>
    <div class="divider"></div>
    <p class="brand">perch &amp; peck</p>
  </section>

  <section class="label one-line green-size" style="left:53px;top:337px;--turn:239deg">
    <div class="face"></div><div class="mark-spot"></div>
    <div class="product-photo" role="img" aria-label="Faded photo of a curled calci worm" style="background:radial-gradient(circle,#e9c9a0,#f4e4cf 60%,#fff)"></div>
    <svg class="rim-text" width="246" height="246" viewBox="-123 -123 246 246" aria-hidden="true"><use href="#label-copy"/></svg>
    <p class="bag-size">5L BAG</p>
    <h2 class="title">CALCI WORMS</h2>
    <p class="specs">SKU: HW24<span class="sep">|</span>Net Weight: 800g</p>
    <p class="ean">EAN 13 BARCODE:</p>
    <div class="divider"></div>
    <p class="brand">perch &amp; peck</p>
  </section>

  <section class="label two-line" style="left:333px;top:337px;--turn:-71deg">
    <div class="face"></div><div class="mark-spot"></div>
    <div class="product-photo" role="img" aria-label="Faded photo of peanuts in their shells" style="background:radial-gradient(circle,#ead7bb,#f4eadb 60%,#fff)"></div>
    <svg class="rim-text" width="246" height="246" viewBox="-123 -123 246 246" aria-hidden="true"><use href="#label-copy"/></svg>
    <p class="bag-size">5L BAG</p>
    <h2 class="title">PEANUTS IN<br>SHELL</h2>
    <p class="specs">SKU: HW25<span class="sep">|</span>Net Weight: 1350g</p>
    <p class="ean">EAN 13 BARCODE:</p>
    <div class="divider"></div>
    <p class="brand">perch &amp; peck</p>
  </section>

  <section class="label one-line green-size" style="left:613px;top:337px;--turn:69deg">
    <div class="face"></div><div class="mark-spot"></div>
    <div class="product-photo" role="img" aria-label="Faded photo of a pile of niger seed" style="background:radial-gradient(circle,#8d8d8d,#c6c6c6 60%,#fff)"></div>
    <svg class="rim-text" width="246" height="246" viewBox="-123 -123 246 246" aria-hidden="true"><use href="#label-copy"/></svg>
    <p class="bag-size">5L BAG</p>
    <h2 class="title">NIGER SEED</h2>
    <p class="specs">SKU: HW26<span class="sep">|</span>Net Weight: 3300g</p>
    <p class="ean">EAN 13 BARCODE:</p>
    <div class="divider"></div>
    <p class="brand">perch &amp; peck</p>
  </section>

  <section class="label two-line" style="left:53px;top:626px;--turn:-151deg">
    <div class="face"></div><div class="mark-spot"></div>
    <div class="product-photo" role="img" aria-label="Faded photo of a mixed wild bird seed pile" style="background:radial-gradient(circle,#c9b08a,#e6d9c3 60%,#fff)"></div>
    <svg class="rim-text" width="246" height="246" viewBox="-123 -123 246 246" aria-hidden="true"><use href="#label-copy"/></svg>
    <p class="bag-size">5L BAG</p>
    <h2 class="title">WILD BIRD<br>MIX</h2>
    <p class="specs">SKU: HW27<span class="sep">|</span>Net Weight: 3300g</p>
    <p class="ean">EAN 13 BARCODE:</p>
    <div class="divider"></div>
    <p class="brand">perch &amp; peck</p>
  </section>

  <section class="label one-line green-size" style="left:333px;top:626px;--turn:129deg">
    <div class="face"></div><div class="mark-spot"></div>
    <div class="product-photo" role="img" aria-label="Faded photo of a no mess seed mix" style="background:radial-gradient(circle,#dcc4a0,#eee2cf 60%,#fff)"></div>
    <svg class="rim-text" width="246" height="246" viewBox="-123 -123 246 246" aria-hidden="true"><use href="#label-copy"/></svg>
    <p class="bag-size">5L BAG</p>
    <h2 class="title">NO MESS MIX</h2>
    <p class="specs">SKU: HW28<span class="sep">|</span>Net Weight: 3200g</p>
    <p class="ean">EAN 13 BARCODE:</p>
    <div class="divider"></div>
    <p class="brand">perch &amp; peck</p>
  </section>

  <section class="label two-line" style="left:613px;top:626px;--turn:-101deg">
    <div class="face"></div><div class="mark-spot"></div>
    <div class="product-photo" role="img" aria-label="Faded photo of peanut granules" style="background:radial-gradient(circle,#e6dccb,#f3eee5 60%,#fff)"></div>
    <svg class="rim-text" width="246" height="246" viewBox="-123 -123 246 246" aria-hidden="true"><use href="#label-copy"/></svg>
    <p class="bag-size">5L BAG</p>
    <h2 class="title">PEANUT<br>GRANULES</h2>
    <p class="specs">SKU: HW29<span class="sep">|</span>Net Weight: 2800g</p>
    <p class="ean">EAN 13 BARCODE:</p>
    <div class="divider"></div>
    <p class="brand">perch &amp; peck</p>
  </section>

  <section class="label two-line green-size" style="left:53px;top:914px;--turn:189deg">
    <div class="face"></div><div class="mark-spot"></div>
    <div class="product-photo" role="img" aria-label="Faded photo of black sunflower seeds" style="background:radial-gradient(circle,#b4b4b4,#dcdcdc 60%,#fff)"></div>
    <svg class="rim-text" width="246" height="246" viewBox="-123 -123 246 246" aria-hidden="true"><use href="#label-copy"/></svg>
    <p class="bag-size">5L BAG</p>
    <h2 class="title">BLACK<br>SUNFLOWER</h2>
    <p class="specs">SKU: HW30<span class="sep">|</span>Net Weight: 2000g</p>
    <p class="ean">EAN 13 BARCODE:</p>
    <div class="divider"></div>
    <p class="brand">perch &amp; peck</p>
  </section>

  <p class="page-code">C58</p>
</div>
</body>
</html>
```